Velora Entertainment

Logo for business card design

Target Market(s)

potential film investors and screenwriters

Industry/Entity Type

Business

Contact Information for Business Card

as shown, website here is a placeholder position

Requirements
Must have
• great visual appeal
Nice to have
• harmony of colors; must evoke spirit of
• U.S.-China cooperation

```html
<!DOCTYPE html>
<html lang="en">
<head>
<meta charset="utf-8">
<title>Velora Entertainment – Business Card</title>
<link rel="stylesheet" href="https://fonts.googleapis.com/css2?family=Open+Sans:wght@400;600;700&display=swap">
<style>
  :root {
    --page: #e3e3e3;
    --card-white: #f4f4f4;
    --brand-red: #c0070f;
    --brand-yellow: #e3c100;
    --brand-navy: #141a78;
    --ink: #1e1e1e;
    --back-light: #8e8f91;
    --back-dark: #7c7d80;
    --on-dark: #ffffff;
  }
  * { box-sizing: border-box; margin: 0; padding: 0; }
  html, body {
    width: 1105px; height: 1200px; overflow: hidden;
    background: var(--page);
    font-family: "Open Sans", Arial, sans-serif;
  }
  .card {
    position: absolute; left: 179px;
    width: 747px; height: 425px;
    box-shadow: 0 6px 14px rgba(0,0,0,.18);
  }
  .card--front { top: 120px; background: var(--card-white); }
  .card--back {
    top: 635px;
    background: linear-gradient(160deg, var(--back-light), var(--back-dark));
  }

  .name-band {
    position: absolute; left: 0; top: 46px;
    width: 446px; height: 115px;
    background: var(--brand-red);
    color: #fff;
    padding: 26px 0 0 44px;
  }
  .name-band__name { font-size: 26px; font-weight: 600; line-height: 1.2; }
  .name-band__title { font-size: 20px; font-weight: 400; line-height: 1.3; }

  .edge-strip {
    position: absolute; left: 708px; top: 46px;
    width: 39px; height: 115px;
    background: var(--brand-navy);
  }

  .wordmark {
    position: absolute;
    display: flex; align-items: center;
    font-weight: 700; line-height: 1.1;
    white-space: nowrap;
  }
  .wordmark__square { flex: none; }
  .wordmark__text { display: flex; flex-direction: column; }
  .wordmark--front {
    left: 458px; top: 75px; gap: 10px;
    color: var(--brand-navy); font-size: 23px;
  }
  .wordmark--front .wordmark__square { width: 34px; height: 34px; background: var(--brand-yellow); }
  .wordmark--back {
    left: 50%; top: 50%; transform: translate(-50%, -50%); gap: 14px;
    color: var(--on-dark); font-size: 40px;
  }
  .wordmark--back .wordmark__square { width: 56px; height: 56px; background: var(--brand-red); }

  .contact-list {
    position: absolute; left: 44px; top: 308px;
    list-style: none; font-size: 19px; color: var(--ink);
  }
  .contact-list li { display: flex; align-items: center; gap: 10px; height: 28px; }
  .contact-list svg { width: 17px; height: 17px; fill: var(--brand-red); flex: none; }

  .address {
    position: absolute; right: 45px; top: 308px;
    font-style: normal; text-align: right;
    font-size: 19px; line-height: 28px; color: var(--ink);
  }
</style>
</head>
<body>

<section class="card card--front" aria-label="Business card front">
  <div class="name-band">
    <p class="name-band__name">Daniel Reyes</p>
    <p class="name-band__title">CEO/Founder</p>
  </div>

  <div class="wordmark wordmark--front">
    <span class="wordmark__square"></span>
    <span class="wordmark__text"><span>Velora</span><span>Entertainment</span></span>
  </div>

  <div class="edge-strip"></div>

  <ul class="contact-list">
    <li>
      <svg viewBox="0 0 24 24" aria-hidden="true"><path d="M6.6 10.8a15.1 15.1 0 0 0 6.6 6.6l2.2-2.2a1 1 0 0 1 1-.25 11.4 11.4 0 0 0 3.6.57 1 1 0 0 1 1 1V20a1 1 0 0 1-1 1A17 17 0 0 1 3 4a1 1 0 0 1 1-1h3.5a1 1 0 0 1 1 1c0 1.25.2 2.450 .57 3.57a1 1 0 0 1-.25 1z"/></svg>
      512 308 4471
    </li>
    <li>
      <svg viewBox="0 0 24 24" aria-hidden="true"><path d="M7 1h10a2 2 0 0 1 2 2v18a2 2 0 0 1-2 2H7a2 2 0 0 1-2-2V3a2 2 0 0 1 2-2zm0 3v14h10V4zm5 15.2a1.2 1.2 0 1 0 0 2.4 1.2 1.2 0 0 0 0-2.4z"/></svg>
      512 774 2086
    </li>
    <li>
      <svg viewBox="0 0 24 24" aria-hidden="true"><path d="M2 5h20v14H2zm2 2v.4l8 5.1 8-5.1V7zm0 2.8V17h16V9.8l-8 5.1z"/></svg>
      hello@velorafilms.com
    </li>
  </ul>

  <address class="address">
    2140 Larkspur Avenue<br>
    Boulder, Colorado 80302<br>
    www.velorafilms.com
  </address>
</section>

<section class="card card--back" aria-label="Business card back">
  <div class="wordmark wordmark--back">
    <span class="wordmark__square"></span>
    <span class="wordmark__text"><span>Velora</span><span>Entertainment</span></span>
  </div>
</section>

</body>
</html>
```